Letter and Envelope Design For Harborline Realty

Please design a letter and an envelope incorporating our logo (See Attached). We are also launched a business card contest. Since we want them to match, please feel free to submit a design for both the business card and also the letter design and envelope.

Requirements
Must have
• The envelope, the letter and the business cards must match somehow connecting the designs. We want them to have something that holds them together besides the logo.

```html
<!DOCTYPE html>
<html lang="en">
<head>
<meta charset="utf-8">
<title>Harborline Realty Stationery</title>
<link rel="stylesheet" href="https://fonts.googleapis.com/css2?family=Montserrat:wght@500&family=Roboto:wght@400;500&family=Allura&display=swap">
<style>
:root{
  --stage:#676767;
  --paper:#f6f6f5;
  --brand:#031a8a;
  --ink:#333;
  --soft:#6d6d6d;
  --ghost:#e6e6e6;
}
*{margin:0;padding:0;box-sizing:border-box}
html,body{width:1200px;height:816px;overflow:hidden}
body{background:var(--stage);position:relative;font-family:'Roboto',sans-serif;color:var(--ink)}
.sheet{position:absolute;background:var(--paper);overflow:hidden}
.envelope-front{left:140px;top:220px;width:474px;height:214px}
.envelope-back{left:140px;top:456px;width:474px;height:213px}
.letter{left:667px;top:130px;width:392px;height:554px}
.ghost-ring{position:absolute;border-radius:50%;border:9px solid var(--ghost)}
.envelope-front .ghost-ring{left:270px;top:-10px;width:250px;height:250px}
.letter .ghost-ring{left:75px;top:154px;width:248px;height:248px}
.brand-tab{position:absolute;left:0;top:0}

.wordmark{position:absolute;display:flex;align-items:center;gap:8px;color:#fff;font-family:'Montserrat',sans-serif;font-weight:500;text-transform:uppercase;white-space:nowrap}
.wordmark .dot{border:1.5px solid #fff;border-radius:50%;flex:none}
.wordmark .name{display:flex;flex-direction:column;align-items:center;line-height:1.15}
.wordmark .name-top{letter-spacing:1.6px}
.wordmark .name-bottom{letter-spacing:3px;font-size:.72em}

.envelope-front .wordmark{left:20px;top:16px;font-size:10px}
.envelope-front .wordmark .dot{width:25px;height:25px}
.letter .wordmark{left:26px;top:23px;font-size:12.5px;gap:10px}
.letter .wordmark .dot{width:33px;height:33px}
.letter .wordmark .name-top{letter-spacing:2px}
.envelope-back .wordmark{left:0;right:0;top:26px;justify-content:center;font-size:11px}

.contact{position:absolute;font-size:6.8px;line-height:9.6px;color:#222}
.contact .row{display:flex;align-items:center;gap:4px}
.contact svg{width:6px;height:6px;fill:var(--brand);flex:none}
.contact .gap{margin-left:5px}
.envelope-front .contact{left:20px;top:165px}
.letter .contact{left:25px;top:525px;font-size:7px}

.letter-body{position:absolute;left:25px;top:100px;width:343px;font-size:5.3px;line-height:8.9px;color:var(--soft)}
.letter-body p{margin-bottom:8.9px;text-align:justify}
.letter-body .recipient b{color:var(--ink);font-weight:500}
.sign{position:absolute;left:25px;top:402px;font-size:5.6px;color:var(--soft)}
.sign .signer{color:var(--ink);font-weight:500}
.sign .script{font-family:'Allura',cursive;font-size:15px;color:var(--brand);margin:3px 0 5px;line-height:16px}
.web-band{position:absolute;left:233px;top:534px;width:159px;height:20px;background:var(--brand);clip-path:polygon(3% 0,100% 0,100% 100%,0 100%);color:#fff;font-size:6.4px;display:flex;align-items:center;justify-content:flex-end;padding-right:20px}
</style>
</head>
<body>

<section class="sheet envelope-front">
  <div class="ghost-ring"></div>
  <svg class="brand-tab" width="172" height="54" viewBox="0 0 172 54"><path d="M0 0H170L161 49Q160 54 155 54H0Z" fill="var(--brand)"/></svg>
  <div class="wordmark"><span class="dot"></span><span class="name"><span class="name-top">Harborline</span><span class="name-bottom">Realty</span></span></div>
  <div class="contact">
    <div class="row"><svg viewBox="0 0 10 10"><path d="M2 1l2 2-1 1.5c.8 1.4 1.6 2.2 3 3L7.5 6l2 2-1.5 1.5C4.5 9 1 5.5.5 2.5z"/></svg>555.013.2048</div>
    <div class="row"><svg viewBox="0 0 10 10"><circle cx="5" cy="5" r="4.5"/></svg>hello@harborlinerealty.com<svg class="gap" viewBox="0 0 10 10"><rect x="1" y="2" width="8" height="6" rx="1"/></svg>www.harborlinerealty.com</div>
    <div class="row"><svg viewBox="0 0 10 10"><path d="M5 0a3.5 3.5 0 0 1 3.5 3.5C8.5 6 5 10 5 10S1.5 6 1.5 3.5A3.5 3.5 0 0 1 5 0z"/></svg>48 Quayside Road, Port Linden, US 10482</div>
  </div>
</section>

<section class="sheet envelope-back">
  <svg class="brand-tab" width="474" height="77" viewBox="0 0 474 77"><path d="M0 0H474L436 70Q432 76 420 76H60Q45 76 40 68Z" fill="var(--brand)"/></svg>
  <div class="wordmark"><span class="name"><span class="name-top">Harborline</span><span class="name-bottom">Realty</span></span></div>
</section>

<section class="sheet letter">
  <div class="ghost-ring"></div>
  <svg class="brand-tab" width="214" height="67" viewBox="0 0 214 67"><path d="M0 0H213L202 62Q201 66 196 66H0Z" fill="var(--brand)"/></svg>
  <div class="wordmark"><span class="dot"></span><span class="name"><span class="name-top">Harborline</span><span class="name-bottom">Realty</span></span></div>
  <div class="letter-body">
    <p>30/20/2016</p>
    <p class="recipient"><b>Mr. Daniel Reeve</b><br>123, Street No. 123,<br>City Name<br>Pincode-123456</p>
    <p>Dear Sir,</p>
    <p>Lorem Ipsum is simply dummy text of the printing and typesetting industry. Lorem Ipsum has been the industry's standard dummy text ever since the 1500s, when an unknown printer took a galley of type and scrambled it to make a type specimen book. It has survived not only five centuries, but also the leap into electronic typesetting, remaining essentially unchanged. It was popularised in the 1960s with the release of Letraset sheets containing Lorem Ipsum passages, and more recently with desktop publishing software including versions of Lorem Ipsum.</p>
    <p>Lorem Ipsum is simply dummy text of the printing and typesetting industry. Lorem Ipsum has been the industry's standard dummy text ever since the 1500s, when an unknown printer took a galley of type and scrambled it to make a type specimen book. It has survived not only five centuries, but also the leap into electronic typesetting, remaining essentially unchanged. It was popularised in the 1960s with the release of Letraset sheets containing Lorem Ipsum passages, and more recently with desktop publishing software including versions of Lorem Ipsum.</p>
    <p>Lorem Ipsum is simply dummy text of the printing and typesetting industry. Lorem Ipsum has been the industry's standard dummy text ever since the 1500s, when an unknown printer took a galley of type and scrambled it to make a type specimen book.</p>
    <p>Lorem Ipsum is simply dummy text of the printing and typesetting industry. Lorem Ipsum has been the industry's standard dummy text ever since the 1500s, when an unknown printer took a galley of type and scrambled it to make a type specimen book.</p>
  </div>
  <div class="sign">
    <div class="signer">Your Name</div>
    <div class="script">Your Signature</div>
    <div>CEO | Owner</div>
  </div>
  <div class="contact">
    <div class="row"><svg viewBox="0 0 10 10"><path d="M2 1l2 2-1 1.5c.8 1.4 1.6 2.2 3 3L7.5 6l2 2-1.5 1.5C4.5 9 1 5.5.5 2.5z"/></svg>555.013.2048<svg class="gap" viewBox="0 0 10 10"><rect x="1" y="2" width="8" height="6" rx="1"/></svg>hello@harborlinerealty.com</div>
    <div class="row"><svg viewBox="0 0 10 10"><path d="M5 0a3.5 3.5 0 0 1 3.5 3.5C8.5 6 5 10 5 10S1.5 6 1.5 3.5A3.5 3.5 0 0 1 5 0z"/></svg>48 Quayside Road, Port Linden, US 10482</div>
  </div>
  <div class="web-band">www.harborlinerealty.com</div>
</section>

</body>
</html>
```